I have a tallow based business and I want to streamline my products

I have roughly 10 items that I would like to make lebals for in order to streamline my business, I am attaching the current design and am willing to work with this but would also like to see if you come up with something different, my biggest seller is my facewash , my webpage is meadowhearthco,com my current designs are below- The newest one is the light brown version which I do like but I am not sure how that will integrate or be streamlined with the remaining products, If you believe it can look similar and still be attractive, I am ok with that too,

My current Label Project Needs:

Tallow + Magnesium Lotion biodegradable wheat bottle
Tallow Cream Face Wash - biodegradable what bottle
Tallow Body Butter 8 oz jar with bamboo lid
Tallow Deodorant will be printed on a Kraft Paper tube
Tallow Face Cream for Day wear 2 oz glass jar with bamboo lid
Vitamin C Serum 2 oz serum bottle with bamboo pump
Blue Algae Toner 4 oz glass bottle
Tallow + Hyaluronic 2oz face cream jar
'
My project is to display sustainable products, eco friendly packaging, organic , natural and holistic

I am ok with the newest label I attached but I am also ok with a minimalistic project, I would love to choose from a couple of designs.

Thank you so much

```html
<!DOCTYPE html>
<html lang="en">
<head>
<meta charset="utf-8">
<title>Meadow Hearth Organics – Face Cream Label</title>
<link rel="stylesheet" href="https://fonts.googleapis.com/css2?family=Jost:wght@400;500;700&family=Philosopher:wght@700&family=Tenor+Sans&family=Tinos:wght@700&family=Lato:wght@400&display=swap">
<style>
  :root {
    --canvas: #e9e9e9;
    --navy: #11152a;
    --gold: #c8b68e;
    --white: #ffffff;
    --rule: rgba(255,255,255,0.75);
  }
  * { margin: 0; padding: 0; box-sizing: border-box; }
  html, body { width: 943px; height: 1200px; overflow: hidden; background: var(--canvas); }
  .stage { position: relative; width: 943px; height: 1200px; }
  .label {
    position: absolute; left: 0; top: 0;
    width: 1067px; height: 662px;
    background: var(--navy);
    border-radius: 18px;
    transform: translate(41.5px, 333px) scale(0.806);
    transform-origin: top left;
    color: var(--white);
    font-family: "Jost", sans-serif;
  }

  /* Feature list */
  .features { position: absolute; left: 81px; top: 70px; width: 256px; }
  .feature {
    height: 104px; display: flex; align-items: center; gap: 22px;
    padding-left: 32px; border-bottom: 1px solid var(--rule);
    font-size: 21px; line-height: 1.05; font-weight: 400;
  }
  .feature:last-child { border-bottom: none; }
  .feature-icon { width: 42px; height: 42px; flex: none; }
  .maker {
    position: absolute; left: 81px; top: 499px; width: 256px; height: 86px;
    border: 1.5px solid var(--white); border-radius: 5px;
    text-align: center; font-size: 11.5px; line-height: 17px; padding-top: 8px;
  }
  .maker strong { font-weight: 700; }

  /* Centre panel */
  .front { position: absolute; left: 400px; top: 0; width: 300px; text-align: center; }
  .brand-mark { position: absolute; left: 141px; top: 64px; width: 18px; height: 18px; border-radius: 50%; background: var(--gold); }
  .brand { position: absolute; left: 0; width: 300px; top: 106px; font-family: "Tenor Sans", sans-serif; font-size: 17.5px; letter-spacing: 2px; }
  .title {
    position: absolute; left: 0; width: 300px; top: 140px;
    font-family: "Philosopher", sans-serif; font-weight: 700;
    font-size: 78px; line-height: 68px;
  }
  .variant {
    position: absolute; left: 30px; top: 315px; width: 241px; height: 38px;
    border: 1.5px solid var(--gold); border-radius: 0 10px 10px 10px / 0 10px 10px 10px;
    border-radius: 4px 12px 4px 12px;
    color: var(--gold); font-size: 23px; letter-spacing: 1.5px; line-height: 36px;
  }
  .cow-art { position: absolute; left: 71px; top: 387px; width: 160px; height: 100px; }
  .benefits { position: absolute; left: 0; width: 300px; top: 520px; color: var(--gold); font-size: 19.5px; }
  .net-wt { position: absolute; left: 0; width: 300px; top: 568px; font-size: 13px; }

  /* Ingredients, set sideways */
  .ingredients {
    position: absolute; left: 793px; top: 587px;
    width: 480px; height: 192px;
    transform: rotate(-90deg); transform-origin: top left;
  }
  .ingredients-heading {
    display: inline-block; width: 298px; height: 28px;
    background: var(--gold); color: var(--navy);
    font-family: "Tinos", serif; font-weight: 700; font-size: 18px;
    line-height: 28px; padding-left: 6px;
  }
  .ingredients-list {
    margin-top: 14px; font-family: "Lato", sans-serif; font-size: 14.6px;
    line-height: 19.2px; letter-spacing: 0.6px; text-align: justify; color: var(--white);
  }
</style>
</head>
<body>
<main class="stage">
  <section class="label">
    <ul class="features">
      <li class="feature"><svg class="feature-icon" role="img" aria-label="Cow head icon" viewBox="0 0 42 42"><rect x="9" y="6" width="24" height="30" rx="6" fill="none" stroke="#fff" stroke-width="2"/></svg><span>Grass Tallow</span></li>
      <li class="feature"><svg class="feature-icon" role="img" aria-label="Leaf in circle icon" viewBox="0 0 42 42"><circle cx="21" cy="21" r="17" fill="none" stroke="#fff" stroke-width="2"/></svg><span>Organic<br>Ingredients</span></li>
      <li class="feature"><svg class="feature-icon" role="img" aria-label="Hands with heart icon" viewBox="0 0 42 42"><rect x="8" y="8" width="26" height="26" rx="8" fill="none" stroke="#fff" stroke-width="2"/></svg><span>Hand Crafted</span></li>
      <li class="feature"><svg class="feature-icon" role="img" aria-label="Handshake icon" viewBox="0 0 42 42"><rect x="5" y="12" width="32" height="18" rx="6" fill="none" stroke="#fff" stroke-width="2"/></svg><span>Fair Trade</span></li>
    </ul>
    <div class="maker">MANUFACTURED BY<br><strong>MEADOW HEARTH ORGANICS</strong><br>PO. BOX : 1180 ASHBROOK, VA 24410<br>meadowhearthco.com</div>

    <div class="front">
      <span class="brand-mark"></span>
      <p class="brand">MEADOW HEARTH ORGANICS</p>
      <h1 class="title">FACE<br>CREAM</h1>
      <p class="variant">TALLOW CREAM</p>
      <svg class="cow-art" role="img" aria-label="White silhouette of a standing cow" viewBox="0 0 160 100"><rect width="160" height="100" rx="10" fill="#ffffff"/></svg>
      <p class="benefits">Cleanse • Purify • Moisturize</p>
      <p class="net-wt">NET WT. 8 OZ (236ML)</p>
    </div>

    <div class="ingredients">
      <h2 class="ingredients-heading">Our Amazing Ingredients:</h2>
      <p class="ingredients-list">Distilled Water, Lavender Hydrosol, Glycerin, Grass Fed Tallow, Daucus Carota (Carrot Seed Oil), Oenothera Biennis (Rosehip Oil), Simmondsia Chinensis(Jojoba Oil) Cocos Nucifera (Coconut Oil), Cucurbita Pepo Seed Oil (Pumpkin Seed Oil)Coenzyme Q10 ( CoQ10 )Niacinamide, Vitamin B3 Citrus Paradisi Seed Oil (Grapefruit Seed oil), Decyl Glucoside, Cetyl Alcohol Citric Acid, Xanthan Gum, Sodium Benzoate (Preservative)</p>
    </div>
  </section>
</main>
</body>
</html>
```